Window Treatment business needs website redesigned.

We need a revamp and refresh of our current site www.velmarix.ca
Looking to attract very high end customer. It should be a very simple design with very little text. This site will be visited by prospective homeowners, designers, builders and architects. They should feel that they are dealing with a high-end product selection, where experience, customer service and unique product offering is the focus. The content will be to highlight our services and highlight the manufacturers we sell, using a few rich photos to highlight the products. We should NOT look like we are a very large company. It should NOT have discounts/savings buttons and many menus to choose from. We offer over 15 years experience to narrow the many market options, to provide the right technical solution.
We specialize in products that are not readily available on the market and specifically motorized systems for indoors and outdoors.
Our main suppliers are Kravenholt.com, Dimbrell.com
We carry our own locally manufactured product line of roller shades.
Main product pictures should be of roller shades, outdoor bug screens, awnings and outdoor pergolas.

Reason: I understand that Christmas is coming up real short and many people are extremely busy. If you have a CREATIVE gifting you still want to submit, I look forward to your idea!

Reason: Due to holiday season, we have not had sufficient time to review to make a final decision. Thank you for your patience!

Target Market(s)

High end home owners, designers, builders, architects

Industry/Entity Type

Contractor

Coding

Coded - Design and coding required

Number of Pages Required

3 page

Font styles to use
Sans Serif

Requirements
Must have
• Landing page with full size image like homepage of zolvane.it
• Products page that highlights products with simple product shot image, description and link to manufacturer.
• On main page a scrolling of customer reviews.
• I want a very simple, eye-catching, emotional image for homepage. It does not need to include any product image.
• An image that shows technology combining/meshing with hand craftsmanship.
• Focus is on design.
• http://www.zolvane.it/en/gallery is a great layout and design.
Nice to have
• Logo shape for icons and watermark should be used.
• Look like and have simple motion effects like quorix.com or telvarin.com
Should not have
• Generic/standard looking feel like bluppet.com or mecklorwindow.ca
• No use of green as background only subtle text.
• Lots of text and pages.

```html
<!DOCTYPE html>
<html lang="en">
<head>
<meta charset="utf-8">
<title>Velmarix – Window Treatment Solutions</title>
<link href="https://fonts.googleapis.com/css2?family=Montserrat:wght@400;500;700&family=Open+Sans:wght@400;600&display=swap" rel="stylesheet">
<style>
:root{
  --green:#5cb947;
  --ink:#111;
  --text:#555;
  --white:#fff;
  --slate-1:#4a5562;
  --slate-2:#2f3741;
  --footer:#2f2f2f;
}
*{box-sizing:border-box;margin:0;padding:0}
h1,h2,h3{font-weight:400}
html,body{width:1200px;height:3098px;overflow:hidden}
body{position:relative;background:var(--white);font-family:"Open Sans",Arial,sans-serif;color:var(--ink)}
.abs{position:absolute}
.heading{font-family:"Montserrat",Arial,sans-serif;font-weight:400;text-transform:uppercase}

/* hero */
.hero{left:0;top:0;width:1200px;height:730px;background:linear-gradient(180deg,#3e4a5e 0%,#6f7e93 45%,#8a8f8c 75%,#5a5650 100%)}
.hero-shape{left:0;top:600px}
.brand{left:78px;top:22px;display:flex;align-items:center;gap:14px}
.brand-dot{width:86px;height:86px;border-radius:50%;background:var(--white)}
.brand-name{font-family:"Montserrat",sans-serif;font-size:46px;line-height:1;color:var(--white)}
.brand-tag{font-family:"Montserrat",sans-serif;font-size:17px;color:var(--white);margin-top:4px}
.contact{right:80px;top:20px;display:flex;align-items:center;gap:14px;font-family:"Montserrat",sans-serif;font-size:23px;color:var(--white)}
.contact b{color:var(--green);font-weight:400}
.phone-ring{width:40px;height:40px;border:2px solid var(--green);border-radius:50%;display:flex;align-items:center;justify-content:center}
.nav{right:82px;top:84px;display:flex;gap:40px;font-family:"Montserrat",sans-serif;font-size:17px;color:var(--green)}
.hero-title{left:0;width:1200px;top:232px;text-align:center;font-family:"Montserrat",sans-serif;font-weight:500;font-size:82px;color:var(--white)}
.hero-sub{left:0;width:1200px;top:334px;text-align:center;font-size:24px;color:var(--white)}
.btn{left:423px;top:434px;width:354px;height:62px;border-radius:31px;background:var(--green);color:var(--white);font-family:"Montserrat",sans-serif;font-size:22px;display:flex;align-items:center;justify-content:center;text-transform:uppercase}

/* welcome */
.welcome-dot{left:576px;top:677px;width:48px;height:48px;border-radius:50%;border:4px solid var(--ink)}
.welcome-title{left:0;width:1200px;top:736px;text-align:center;font-family:"Montserrat",sans-serif;font-size:38px;text-transform:uppercase}
.welcome-title span{text-transform:none;color:var(--green)}
.welcome-text{left:200px;width:800px;top:800px;text-align:center;font-size:14px;line-height:23px;color:var(--text)}

/* services */
.row{left:0;width:1200px}
.row-dark{background:linear-gradient(135deg,var(--slate-1),var(--slate-2) 55%,#3d4652)}
.row-gray{background:linear-gradient(135deg,#f4f4f4,#e2e2e2 50%,#f0f0f0)}
.services-title{left:0;width:1200px;top:966px;text-align:center;font-size:40px;color:var(--white)}
.svc-name{font-family:"Montserrat",sans-serif;font-size:32px;font-weight:400;text-transform:uppercase}
.on-dark .svc-name{color:var(--white)}
.svc-text{font-size:15.5px;line-height:25px;margin-top:8px;width:560px}
.on-dark{color:var(--white)}
.on-gray .svc-text{color:#333}

/* manufacturers */
.makers-title{left:0;width:1200px;top:2386px;text-align:center;font-size:37px}
.makers{left:80px;width:1040px;top:2485px;display:flex;justify-content:space-between;align-items:center;font-family:"Montserrat",sans-serif;font-size:17px;font-weight:700;color:#2c4f8c}
.maker{display:flex;align-items:center;gap:6px}
.maker i{display:inline-block;width:16px;height:16px;background:#c8262c}

/* testimonials */
.quotes{left:0;top:2570px;width:1200px;height:412px;background:linear-gradient(180deg,#4a5562,#2f3741)}
.quotes-title{left:0;width:1200px;top:2656px;text-align:center;font-size:37px;color:var(--white)}
.quote-box{left:237px;top:2718px;width:727px;height:106px;background:var(--white);border-radius:4px;padding:16px 40px;text-align:center;font-size:14px;line-height:23px;color:#444}
.quote-tail{left:588px;top:2822px}
.avatar{left:558px;top:2847px;width:82px;height:82px;border-radius:50%;border:4px solid var(--white);background:linear-gradient(180deg,#c9b9a8,#5b6470)}
.author{left:668px;top:2874px;font-family:"Montserrat",sans-serif;font-size:18px;color:var(--white)}
.author small{font-family:"Open Sans",sans-serif;font-style:italic;font-size:13px}

/* footer */
.footer{left:0;top:2982px;width:1200px;height:116px;background:var(--footer)}
.footnav{left:78px;top:3012px;display:flex;font-family:"Montserrat",sans-serif;font-size:14px;color:var(--white)}
.footnav span{padding:0 15px;border-left:1px solid #666}
.footnav span:first-child{padding-left:0;border-left:0}
.copy{left:78px;top:3049px;font-size:13px;color:var(--white)}
.copy b{color:var(--green);font-weight:400}
.social{right:76px;top:3010px;display:flex;gap:19px}
.social i{display:block;width:54px;height:54px;border-radius:50%;border:3px solid var(--white)}
.social i:first-child{border-color:var(--green)}
</style>
</head>
<body>

<div class="abs hero" role="img" aria-label="Photo of a bright home office with dark motorized roller shades lowered over the windows"></div>
<svg class="abs hero-shape" width="1200" height="130" viewBox="0 0 1200 130" aria-hidden="true">
  <polygon points="0,110 600,14 1200,110 1200,130 0,130" fill="#fff"/>
  <polyline points="0,110 600,14 1200,110" fill="none" stroke="#5cb947" stroke-width="6"/>
</svg>

<header>
  <div class="abs brand">
    <div class="brand-dot"></div>
    <div>
      <div class="brand-name">Velmarix</div>
      <div class="brand-tag">Window Treatment Solutions</div>
    </div>
  </div>
  <div class="abs contact">
    <span class="phone-ring">
      <svg width="20" height="20" viewBox="0 0 24 24"><path d="M6.6 10.8a15 15 0 0 0 6.6 6.6l2.2-2.2c.3-.3.7-.4 1-.2 1.1.4 2.3.6 3.6.6.6 0 1 .4 1 1V20c0 .6-.4 1-1 1A17 17 0 0 1 3 4c0-.6.4-1 1-1h3.5c.6 0 1 .4 1 1 0 1.3.2 2.5.6 3.6.1.3 0 .7-.2 1z" fill="#5cb947"/></svg>
    </span>
    CONTACT US NOW <b>416-555-0142</b>
  </div>
  <nav class="abs nav"><span>Home</span><span>About</span><span>Services</span><span>Product</span><span>Gallery</span><span>Contact</span></nav>
</header>

<h1 class="abs hero-title">Motorized Shades</h1>
<p class="abs hero-sub">We offer both top-of-the-line and affordable automated blinds.</p>
<div class="abs btn">Start your project</div>

<section>
  <div class="abs welcome-dot"></div>
  <h2 class="abs welcome-title">Welcome to <span>Velmarix</span></h2>
  <p class="abs welcome-text">We offer over 15 years experience to narrow the many market options, to provide the right technical solution.<br>We specialize in products that are not readily available on the market and specifically motorized systems for indoors and outdoors.</p>
</section>

<section>
  <div class="abs row row-dark" style="top:917px;height:416px" role="img" aria-label="Photo of a modern living space with roller shades, under a dark wash"></div>
  <h2 class="abs heading services-title">Services</h2>
  <div class="abs on-dark" style="left:80px;top:1101px">
    <h3 class="svc-name">Roller Shades</h3>
    <p class="svc-text">Lorem Ipsum is simply dummy text of the printing and typesetting industry. Lorem Ipsum has been the industry's standard dummy text ever since the 1500s.</p>
  </div>
  <svg class="abs" style="left:776px;top:1052px" width="226" height="226" viewBox="0 0 226 226" aria-hidden="true">
    <circle cx="113" cy="113" r="110" fill="#fff"/>
    <circle cx="103" cy="108" r="98" fill="#fff" stroke="#111" stroke-width="7"/>
    <rect x="62" y="58" width="84" height="104" fill="none" stroke="#111" stroke-width="6"/>
    <line x1="104" y1="58" x2="104" y2="162" stroke="#111" stroke-width="5"/>
    <g stroke="#111" stroke-width="4">
      <line x1="62" y1="70" x2="146" y2="70"/><line x1="62" y1="80" x2="146" y2="80"/><line x1="62" y1="90" x2="146" y2="90"/><line x1="62" y1="100" x2="146" y2="100"/><line x1="62" y1="110" x2="146" y2="110"/>
    </g>
    <line x1="140" y1="114" x2="140" y2="140" stroke="#111" stroke-width="2"/>
  </svg>

  <div class="abs row row-gray" style="top:1336px;height:332px" role="img" aria-label="Photo of a bright room with sheer drapery panels, faded"></div>
  <svg class="abs" style="left:205px;top:1392px" width="216" height="216" viewBox="0 0 216 216" aria-hidden="true">
    <circle cx="108" cy="108" r="100" fill="#fff" stroke="#111" stroke-width="8"/>
    <rect x="50" y="52" width="116" height="12" fill="#111"/>
    <path d="M56 64 L56 160 L96 160 Q76 120 88 64 Z" fill="#111"/>
    <path d="M160 64 L160 160 L120 160 Q140 120 128 64 Z" fill="#111"/>
    <rect x="92" y="70" width="32" height="76" fill="none" stroke="#111" stroke-width="4"/>
  </svg>
  <div class="abs on-gray" style="left:555px;top:1428px">
    <h3 class="svc-name">Drapery</h3>
    <p class="svc-text">Lorem Ipsum is simply dummy text of the printing and typesetting industry. Lorem Ipsum has been the industry's standard dummy text ever since the 1500s.</p>
  </div>

  <div class="abs row row-dark" style="top:1669px;height:333px" role="img" aria-label="Photo of an outdoor deck with a retractable awning, under a dark wash"></div>
  <div class="abs on-dark" style="left:80px;top:1762px">
    <h3 class="svc-name">Awnings</h3>
    <p class="svc-text">Lorem Ipsum is simply dummy text of the printing and typesetting industry. Lorem Ipsum has been the industry's standard dummy text ever since the 1500s.</p>
  </div>
  <svg class="abs" style="left:776px;top:1720px" width="226" height="226" viewBox="0 0 226 226" aria-hidden="true">
    <circle cx="113" cy="113" r="110" fill="#fff"/>
    <circle cx="103" cy="108" r="98" fill="#fff" stroke="#111" stroke-width="7"/>
    <path d="M48 70 L60 50 L146 50 L158 70 Z" fill="#111"/>
    <rect x="48" y="70" width="110" height="16" fill="none" stroke="#111" stroke-width="6"/>
    <rect x="58" y="86" width="90" height="72" fill="none" stroke="#111" stroke-width="7"/>
    <rect x="72" y="104" width="24" height="54" fill="none" stroke="#111" stroke-width="6"/>
    <rect x="108" y="104" width="28" height="26" fill="none" stroke="#111" stroke-width="6"/>
  </svg>

  <div class="abs row row-gray" style="top:2003px;height:334px" role="img" aria-label="Photo of a sunroom with screened windows, faded"></div>
  <svg class="abs" style="left:205px;top:2056px" width="216" height="216" viewBox="0 0 216 216" aria-hidden="true">
    <circle cx="108" cy="108" r="100" fill="#fff" stroke="#111" stroke-width="8"/>
    <path d="M108 44 L170 100 L156 100 L156 162 L60 162 L60 100 L46 100 Z" fill="#111"/>
    <rect x="70" y="52" width="16" height="30" fill="#111"/>
    <rect x="96" y="110" width="26" height="52" fill="#fff"/>
  </svg>
  <div class="abs on-gray" style="left:555px;top:2096px">
    <h3 class="svc-name">Bug Screens</h3>
    <p class="svc-text">Lorem Ipsum is simply dummy text of the printing and typesetting industry. Lorem Ipsum has been the industry's standard dummy text ever since the 1500s.</p>
  </div>
</section>

<section>
  <h2 class="abs heading makers-title">Manufacturers we work for</h2>
  <div class="abs makers">
    <span class="maker">DIMBRELL</span>
    <span class="maker"><i></i>HARNVELD</span>
    <span class="maker">Quietrail</span>
    <span class="maker">Brenvoro</span>
    <span class="maker" style="color:#c8262c">TESSALY</span>
    <span class="maker" style="color:#333">Lumarest</span>
    <span class="maker" style="color:#c8262c">Orvanne</span>
    <span class="maker" style="color:#333">Veilcraft</span>
  </div>
</section>

<section>
  <div class="abs quotes" role="img" aria-label="Collage of client portrait photos under a dark wash"></div>
  <svg class="abs" style="left:0;top:2560px" width="1200" height="80" viewBox="0 0 1200 80" aria-hidden="true">
    <polygon points="0,0 1200,0 1200,74 600,10 0,74" fill="#fff"/>
    <polyline points="0,74 600,10 1200,74" fill="none" stroke="#5cb947" stroke-width="6"/>
  </svg>
  <h2 class="abs heading quotes-title">What clients say</h2>
  <p class="abs quote-box">" Lorem Ipsum is simply dummy text of the printing and typesetting industry. Lorem Ipsum has been the industry's standard dummy text ever since the 1500s, when an unknown printer took a galley of type and scrambled it to make a type specimen book. "</p>
  <svg class="abs quote-tail" width="24" height="14" viewBox="0 0 24 14" aria-hidden="true"><polygon points="0,0 24,0 12,14" fill="#fff"/></svg>
  <div class="abs avatar" role="img" aria-label="Client portrait photo"></div>
  <p class="abs author">Dana K., <small>Halden-ON (Northgate)</small></p>
</section>

<footer>
  <div class="abs footer"></div>
  <nav class="abs footnav"><span>HOME</span><span>ABOUT</span><span>SERVICES</span><span>PRODUCTS</span><span>GALLERY</span><span>CONTACT</span></nav>
  <p class="abs copy">© <b>VELMARIX</b> – 2016. All Rights Reserved.</p>
  <div class="abs social" aria-label="Social links"><i></i><i></i><i></i><i></i></div>
</footer>

</body>
</html>
```